Modern business card design for professional copywriter

I'd like a business card design that I can use to have my cards printed out by quillprint.com as a squared corners business card (see artwork and design guidelines here: https://help.quillprint.com/hc/en-gb/sections/200570950-QUILL-Product-Templates)

The design should be clean and modern and reflect the colours, tone and branding on my website: https://tessavorrin.com.au

Target Market(s)

Professionals, B2B small business owners

Industry/Entity Type

Business

Contact Information for Business Card

Tessa Vorrin
m: 0468 905 327
e: tessa@tessavorrin.com.au
w: tessavorrin.com.au

Font styles to use
Sans Serif

Requirements
Must have
• Tagline: "Smart copywriting for clever business people"
• Brand colours: fd8000, 009984, 666666 and black
Nice to have

```html
<!DOCTYPE html>
<html lang="en">
<head>
<meta charset="utf-8">
<title>Tessa Vorrin – Business Card</title>
<link rel="stylesheet" href="https://fonts.googleapis.com/css2?family=Jost:wght@400;500&display=swap">
<style>
  :root {
    --bg: #ecebe8;
    --teal: #149e87;
    --teal-deep: #0f8e79;
    --orange: #fd8000;
    --grey: #666666;
    --ink: #222222;
    --white: #ffffff;
  }
  * { margin: 0; padding: 0; box-sizing: border-box; }
  html, body {
    width: 1200px; height: 929px; overflow: hidden;
    background: var(--bg);
    font-family: "Jost", sans-serif;
  }
  .canvas { position: relative; width: 1200px; height: 929px; }

  .card {
    position: absolute;
    width: 560px; height: 362px;
    overflow: hidden;
    box-shadow: 0 6px 14px rgba(0,0,0,0.18);
  }

  /* Back of card */
  .card-back { left: 70px; top: 80px; background: var(--teal); }
  .card-back .map-area {
    position: absolute; left: 50px; top: 30px; width: 470px; height: 300px;
    background: radial-gradient(ellipse at center, rgba(10,120,100,0.35) 0%, rgba(10,120,100,0.12) 60%, rgba(10,120,100,0) 80%);
  }
  .card-back .brand {
    position: absolute; left: 0; right: 0; top: 150px;
    display: flex; justify-content: center; align-items: center; gap: 12px;
  }
  .brand-mark { width: 16px; height: 16px; }
  .card-back .brand-mark { background: var(--white); }
  .card-back .brand-name { color: var(--white); font-size: 40px; font-weight: 400; letter-spacing: 0.5px; }

  /* Front of card */
  .card-front { left: 570px; top: 480px; background: var(--white); }
  .card-front .brand {
    position: absolute; left: 48px; top: 72px;
    display: flex; align-items: center; gap: 10px;
  }
  .card-front .brand-mark { background: var(--orange); }
  .card-front .brand-name { color: var(--teal); font-size: 34px; font-weight: 400; }

  .side-tab {
    position: absolute; right: -12px; top: 58px;
    width: 24px; height: 42px; border-radius: 12px;
    border: 3px solid var(--teal);
  }

  .identity { position: absolute; right: 40px; top: 112px; text-align: right; }
  .identity .person { color: var(--teal); font-size: 23px; line-height: 1.1; }
  .identity .role { color: var(--ink); font-size: 20px; line-height: 1.15; }

  .rule {
    position: absolute; left: 110px; right: 130px; top: 180px;
    height: 2px; background: var(--teal);
  }

  .contacts { position: absolute; left: 90px; top: 198px; list-style: none; }
  .contacts li {
    display: flex; align-items: center; gap: 10px;
    color: var(--ink); font-size: 15px; line-height: 24px;
  }
  .contacts svg { width: 13px; height: 13px; flex: none; }

  .tagline {
    position: absolute; right: 40px; bottom: 48px;
    text-align: right; color: var(--ink); font-size: 13px; line-height: 1.3;
  }

  .band-orange { position: absolute; left: 0; bottom: 0; width: 400px; height: 24px; background: var(--orange); }
  .band-teal { position: absolute; right: 0; bottom: 0; width: 154px; height: 36px; background: var(--teal); }
</style>
</head>
<body>
<main class="canvas">

  <section class="card card-back" aria-label="Card back">
    <div class="map-area" role="img" aria-label="Faint world map in darker teal"></div>
    <div class="brand">
      <span class="brand-mark"></span>
      <span class="brand-name">Tessa Vorrin</span>
    </div>
  </section>

  <section class="card card-front" aria-label="Card front">
    <div class="side-tab"></div>
    <div class="brand">
      <span class="brand-mark"></span>
      <span class="brand-name">Tessa Vorrin</span>
    </div>

    <div class="identity">
      <p class="person">Tessa Vorrin</p>
      <p class="role">Copywriter</p>
    </div>

    <div class="rule"></div>

    <ul class="contacts">
      <li>
        <svg viewBox="0 0 12 12" aria-hidden="true"><rect x="3" y="0.8" width="6" height="10.4" rx="1" fill="none" stroke="#fd8000" stroke-width="1.4"/></svg>
        0468 905 327
      </li>
      <li>
        <svg viewBox="0 0 12 12" aria-hidden="true"><rect x="0.5" y="2.5" width="11" height="7.5" fill="#fd8000"/><path d="M0.5 2.5 L6 7 L11.5 2.5" fill="none" stroke="#fff" stroke-width="1"/></svg>
        tessa@tessavorrin.com.au
      </li>
      <li>
        <svg viewBox="0 0 12 12" aria-hidden="true"><circle cx="5" cy="5" r="3.5" fill="none" stroke="#fd8000" stroke-width="1.6"/><line x1="7.6" y1="7.6" x2="11" y2="11" stroke="#fd8000" stroke-width="1.8"/></svg>
        tessavorrin.com.au
      </li>
    </ul>

    <p class="tagline">Smart copywriting for<br>clever business people</p>

    <div class="band-orange"></div>
    <div class="band-teal"></div>
  </section>

</main>
</body>
</html>
```